Very new and innovative Web design for Property managers of Vacation rentals

We are looking for a new website design for travel agencies and property managers specialised on vacation rentals business, holiday villas and apartments.

The end users of this website are travellers who are looking for a vacation home for their next holiday: this is the reason why the website must be easy to use, attractive, professional, possibly elegant and focused on get new reservations.

This is a draft of our current website: https://intro3.kelumsito.com/
Please consider that we would like to have proposals with a totally different and innovative layout, surprise us!

These are the pages of the website:
• Homepage: feel free to redesign all the homepage as you wish, surprise us with something very new! Please consider that Property manager/Travel agencies usually want to have the opportunity to put in evidence groups of houses with specific characteristics (eg. villas with private swimming pool, apartment in big/small towns, villas with air co, etc…), destinations and tourist areas, and sometimes experiences or activities (please consider that the website layout must be suitable even if some of the previous sections are not used).
• Search page: we’d like to organise the results of the search page in three different ways:
o Grid
o Map
o List
• Property page: to illustrate the characteristics, descriptions, images, …. of the property. It is very important to put in evidence images of the property and to maintain the booking form (and the other call to action bottom – eg. whatsapp) always visible
• Custom pages: static pages composed usually by text, images and call to actions
• Contact us (general form)
• Info request (specific of a property form)
• Booking process
• Blog, organised in four pages:
o Home Page – introduction to the blog
o List of articles
o Single article
o Site Map (presentation of categories and sub-categories)

If possible, we’d prefer to receive the material in Adobe XD or similar so that we can obtain the three versions:
- smartphone
- tablet
- desktop

The website will be then developed in Bootstrap: as a result we’ll need the icons in SVG format (or the library used)

In attachment you can find the map of the website pages

```html
<!DOCTYPE html>
<html lang="en">
<head>
<meta charset="utf-8">
<title>StayNest – Search</title>
<link href="https://fonts.googleapis.com/css2?family=Nunito+Sans:wght@400;600;700&family=Playfair+Display:wght@400;700&display=swap" rel="stylesheet">
<style>
:root{
  --green:#10b98a;
  --ink:#2b2f33;
  --muted:#6b7075;
  --line:#e3e6e9;
  --panel:#f4f6f8;
  --footer:#1e1e20;
  --white:#fff;
}
*{box-sizing:border-box;margin:0;padding:0}
html,body{width:932px;height:1200px;overflow:hidden;background:var(--white)}
body{font-family:"Nunito Sans",sans-serif;color:var(--ink)}
.page{position:relative;width:932px;height:1200px;overflow:hidden}
.abs{position:absolute}
/* header */
.brand{left:87px;top:22px;display:flex;align-items:center;gap:7px;font-size:23px;font-weight:600;color:var(--ink)}
.brand-mark{width:16px;height:16px;border-radius:50%;background:var(--green)}
.topbar{left:629px;top:0;width:303px;height:33px;background:var(--green);clip-path:polygon(0 0,100% 0,100% 100%,33px 100%)}
.topbar-links{left:675px;top:0;height:33px;display:flex;align-items:center;gap:19px;color:var(--white);font-size:9px;font-weight:700;letter-spacing:.2px}
.topbar-links span{display:flex;align-items:center;gap:4px}
.nav{top:47px;font-size:10px;color:var(--ink);letter-spacing:.2px}
.nav.active{color:var(--green);font-weight:700}
/* hero */
.hero{left:0;top:72px;width:932px;height:155px;background:linear-gradient(160deg,#4a3a32 0%,#6d4d3e 35%,#3b3f34 65%,#586049 100%)}
.hero::after{content:"";position:absolute;inset:0;background:rgba(0,0,0,.28)}
.hero-title{left:0;width:932px;top:128px;text-align:center;font-family:"Playfair Display",serif;font-weight:700;font-size:35px;color:var(--white);letter-spacing:.3px}
/* filters */
.filters{left:87px;top:194px;width:174px;height:753px;background:var(--panel)}
.filters-head{left:87px;top:194px;width:174px;height:33px;background:var(--white);color:var(--green);font-size:10px;padding:12px 14px}
.clear{left:99px;top:240px;font-size:9px;text-decoration:underline;color:var(--ink)}
.group-label{left:99px;font-size:7px;color:var(--muted);letter-spacing:.2px}
.section-title{left:99px;font-size:10px;color:var(--ink)}
.opt{left:99px;display:flex;align-items:center;gap:7px;font-size:9.5px;color:var(--ink)}
.radio{width:15px;height:15px;border:1px solid #cfd3d7;border-radius:50%;background:var(--white);display:flex;align-items:center;justify-content:center}
.radio.on::after{content:"";width:7px;height:7px;border-radius:50%;background:var(--green)}
.check{width:11px;height:11px;border:1px solid #c9cdd1;background:var(--white);margin-right:2px}
.search-box{left:100px;top:891px;width:148px;height:27px;border:1px solid #cfd3d7;background:var(--white);font-size:8.5px;color:var(--muted);padding:8px 10px}
/* view toggle */
.views{left:663px;top:195px;width:181px;height:34px;background:var(--white);display:flex;font-size:7px;font-weight:600}
.views span{flex:1;display:flex;align-items:center;justify-content:center;gap:4px;color:var(--ink)}
.views .active{background:#f1f3f5;border-bottom:2px solid var(--green)}
/* cards */
.card{width:174px;height:252px;background:var(--white);box-shadow:0 2px 8px rgba(0,0,0,.07)}
.card-photo{width:174px;height:113px}
.card-title{position:absolute;left:11px;top:126px;font-family:"Playfair Display",serif;font-size:12.5px;color:var(--ink)}
.card-type{position:absolute;left:11px;top:143px;font-size:8.5px;color:var(--muted)}
.card-rule{position:absolute;left:8px;right:8px;top:158px;border-top:1px solid var(--line)}
.amen{position:absolute;top:174px;left:25px;display:flex;gap:21px}
.amen svg{width:14px;height:14px;color:var(--green)}
.card-foot{position:absolute;left:0;top:198px;width:174px;height:54px;background:#f6f7f9}
.from{position:absolute;left:14px;top:9px;font-size:8.5px;color:var(--muted);line-height:1.2}
.from b{display:block;font-size:11.5px;color:var(--ink);font-weight:700}
.info-btn{position:absolute;left:87px;top:11px;width:73px;height:31px;background:var(--green);color:var(--white);font-size:10.5px;font-weight:700;display:flex;align-items:center;justify-content:center}
/* pagination */
.showing{left:281px;top:837px;font-size:9.5px;color:var(--muted)}
.pager{left:739px;top:833px;display:flex}
.pager span{width:21px;height:21px;border:1px solid #cfd3d7;margin-left:-1px;display:flex;align-items:center;justify-content:center;font-family:"Playfair Display",serif;font-size:10px;color:var(--muted)}
.pager .cur{color:var(--ink)}
/* footer */
.footer{left:0;top:947px;width:932px;height:253px;background:var(--footer);color:#c9cbce}
.f-brand{left:87px;top:1046px;display:flex;align-items:center;gap:7px;font-size:19px;font-weight:600;color:var(--white)}
.f-head{top:987px;font-family:"Playfair Display",serif;font-size:13.5px;color:var(--white)}
.f-link{font-size:10px;color:#c9cbce}
.f-ico{width:10px;height:10px;color:#e6e7e8}
.social{left:771px;display:flex;align-items:center;gap:6px;font-size:10px;color:#c9cbce}
.social i{width:22px;height:22px;border-radius:50%;background:var(--white);display:block}
.copy{left:0;width:932px;top:1144px;text-align:center;font-size:9px;color:#c9cbce}
.copy b{color:var(--white);font-weight:400}
</style>
</head>
<body>
<svg width="0" height="0" style="position:absolute">
  <symbol id="i-wifi" viewBox="0 0 24 24"><g fill="none" stroke="currentColor" stroke-width="2" stroke-linecap="round"><path d="M3 9a13 13 0 0 1 18 0"/><path d="M6.5 12.5a8 8 0 0 1 11 0"/><path d="M10 16a3 3 0 0 1 4 0"/></g><circle cx="12" cy="19.5" r="1.5" fill="currentColor"/></symbol>
  <symbol id="i-snow" viewBox="0 0 24 24"><g stroke="currentColor" stroke-width="2.2" stroke-linecap="round"><path d="M12 3v18M4.2 7.5l15.6 9M4.2 16.5l15.6-9"/></g></symbol>
  <symbol id="i-pool" viewBox="0 0 24 24"><g fill="none" stroke="currentColor" stroke-width="1.8" stroke-linecap="round"><path d="M8 16V5a2 2 0 0 1 3-1.5M15 16V5a2 2 0 0 1 3-1.5M8 8h7M8 12h7"/><path d="M3 19c2 1.5 4-1.5 6 0s4-1.5 6 0 4-1.5 6 0"/></g></symbol>
  <symbol id="i-bike" viewBox="0 0 24 24"><g fill="none" stroke="currentColor" stroke-width="1.8" stroke-linecap="round"><circle cx="5.5" cy="17" r="3.5"/><circle cx="18.5" cy="17" r="3.5"/><path d="M5.5 17l4-7h6l3 7M9.5 10l3.5 7M14 6h2"/></g><circle cx="15" cy="4" r="1.6" fill="currentColor"/></symbol>
  <symbol id="i-user" viewBox="0 0 24 24"><g fill="none" stroke="currentColor" stroke-width="2"><circle cx="12" cy="8" r="4"/><path d="M4 21a8 8 0 0 1 16 0"/></g></symbol>
  <symbol id="i-heart" viewBox="0 0 24 24"><path d="M12 20s-8-5-8-11a4.5 4.5 0 0 1 8-2.8A4.5 4.5 0 0 1 20 9c0 6-8 11-8 11z" fill="none" stroke="currentColor" stroke-width="2"/></symbol>
  <symbol id="i-pin" viewBox="0 0 24 24"><path d="M12 2a7 7 0 0 0-7 7c0 5 7 13 7 13s7-8 7-13a7 7 0 0 0-7-7zm0 9.5A2.5 2.5 0 1 1 12 6.5a2.5 2.5 0 0 1 0 5z" fill="currentColor"/></symbol>
  <symbol id="i-phone" viewBox="0 0 24 24"><path d="M7 2h3l1.5 5-2 1.5a11 11 0 0 0 6 6l1.5-2 5 1.5v3a2 2 0 0 1-2 2A17 17 0 0 1 5 4a2 2 0 0 1 2-2z" fill="currentColor"/></symbol>
  <symbol id="i-mail" viewBox="0 0 24 24"><path d="M2 5h20v14H2z" fill="currentColor"/><path d="M2 5l10 8 10-8" fill="none" stroke="#1e1e20" stroke-width="1.6"/></symbol>
  <symbol id="i-search" viewBox="0 0 24 24"><g fill="none" stroke="currentColor" stroke-width="2.4" stroke-linecap="round"><circle cx="10" cy="10" r="6.5"/><path d="M15 15l6 6"/></g></symbol>
</svg>

<div class="page">
  <!-- header -->
  <div class="abs brand"><span class="brand-mark"></span>StayNest</div>
  <div class="abs topbar"></div>
  <div class="abs topbar-links">
    <span><svg width="11" height="11"><use href="#i-user"/></svg>LOGIN</span>
    <span><svg width="11" height="11"><use href="#i-heart"/></svg>WHISHLIST</span>
    <span>EN ˅</span>
  </div>
  <div class="abs nav active" style="left:441px">HOME</div>
  <div class="abs nav" style="left:516px">SEARCH</div>
  <div class="abs nav" style="left:599px">PROPERTY</div>
  <div class="abs nav" style="left:694px">CUSTOM</div>
  <div class="abs nav" style="left:780px">CONTACT US</div>

  <!-- hero -->
  <div class="abs hero" role="img" aria-label="Photo of a countryside holiday house with flowering garden"></div>
  <div class="abs hero-title">SEARCH PAGE</div>

  <!-- filters -->
  <div class="abs filters"></div>
  <div class="abs filters-head">FILTERS</div>
  <div class="abs clear">Clear all</div>
  <div class="abs group-label" style="top:259px">TYPE OF ACCOMMODATION</div>
  <div class="abs opt" style="top:293px"><i class="radio on"></i>All</div>
  <div class="abs opt" style="top:317px"><i class="radio"></i>GardenNear</div>
  <div class="abs opt" style="top:341px"><i class="radio"></i>VillageInternet</div>
  <div class="abs opt" style="top:365px"><i class="radio"></i>Baby Bed</div>
  <div class="abs opt" style="top:389px"><i class="radio"></i>Maid</div>
  <div class="abs opt" style="top:413px"><i class="radio"></i>Parking</div>
  <div class="abs opt" style="top:437px"><i class="radio"></i>Swimmingpool</div>
  <div class="abs opt" style="top:461px"><i class="radio"></i>Weddings</div>
  <div class="abs opt" style="top:485px"><i class="radio"></i>Breakfast</div>
  <div class="abs opt" style="top:510px"><i class="radio"></i>Internet Wifi</div>

  <div class="abs section-title" style="top:556px">CATEGORY</div>
  <div class="abs opt" style="top:581px"><i class="check"></i>Sevilla</div>

  <div class="abs section-title" style="top:618px">MAIN FEATURES</div>
  <div class="abs opt" style="top:643px"><i class="check"></i>GardenNear</div>
  <div class="abs opt" style="top:667px"><i class="check"></i>VillageInternet</div>
  <div class="abs opt" style="top:690px"><i class="check"></i>Baby Bed</div>
  <div class="abs opt" style="top:714px"><i class="check"></i>Maid</div>
  <div class="abs opt" style="top:737px"><i class="check"></i>Parking</div>
  <div class="abs opt" style="top:761px"><i class="check"></i>Swimmingpool</div>
  <div class="abs opt" style="top:785px"><i class="check"></i>Weddings</div>
  <div class="abs opt" style="top:808px"><i class="check"></i>Breakfast</div>
  <div class="abs opt" style="top:831px"><i class="check"></i>Internet Wifi</div>

  <div class="abs section-title" style="top:873px;font-size:9px">REFERENCE N° / NAME</div>
  <div class="abs search-box">Search</div>
  <svg class="abs" style="left:228px;top:898px;color:#6b7075" width="12" height="12"><use href="#i-search"/></svg>

  <!-- view toggle -->
  <div class="abs views">
    <span class="active"><svg width="11" height="11" viewBox="0 0 12 12" fill="#2b2f33"><rect x="0" y="0" width="3" height="3"/><rect x="4.5" y="0" width="3" height="3"/><rect x="9" y="0" width="3" height="3"/><rect x="0" y="4.5" width="3" height="3"/><rect x="4.5" y="4.5" width="3" height="3"/><rect x="9" y="4.5" width="3" height="3"/><rect x="0" y="9" width="3" height="3"/><rect x="4.5" y="9" width="3" height="3"/><rect x="9" y="9" width="3" height="3"/></svg>GRID</span>
    <span><svg width="13" height="10" viewBox="0 0 13 10" fill="#6b7075"><rect width="3" height="2"/><rect x="4" width="9" height="2"/><rect y="4" width="3" height="2"/><rect x="4" y="4" width="9" height="2"/><rect y="8" width="3" height="2"/><rect x="4" y="8" width="9" height="2"/></svg>LIST</span>
    <span><svg width="10" height="11" style="color:#6b7075"><use href="#i-pin"/></svg>MAP</span>
  </div>

  <!-- results -->
  <div class="abs card" style="left:282px;top:255px">
    <div class="card-photo" role="img" aria-label="Photo of a modern villa with swimming pool" style="background:linear-gradient(180deg,#c9d6df 0%,#7e8c8e 45%,#2aa3d4 75%,#1f7fb3 100%)"></div>
    <div class="card-title">Agriturismo Il Bianco</div>
    <div class="card-type">Country House / Farm House</div>
    <div class="card-rule"></div>
    <div class="amen"><svg><use href="#i-wifi"/></svg><svg><use href="#i-snow"/></svg><svg><use href="#i-pool"/></svg><svg><use href="#i-bike"/></svg></div>
    <div class="card-foot"><div class="from">from<b>€ 3400</b>per week</div><div class="info-btn">+ Info</div></div>
  </div>
  <div class="abs card" style="left:476px;top:255px">
    <div class="card-photo" role="img" aria-label="Photo of a garden pool with sun loungers" style="background:linear-gradient(180deg,#5c7a3e 0%,#7c9a55 45%,#2c95c9 75%,#1b6fa6 100%)"></div>
    <div class="card-title">Podere Il Pino</div>
    <div class="card-type">Apartment</div>
    <div class="card-rule"></div>
    <div class="amen"><svg><use href="#i-wifi"/></svg><svg><use href="#i-snow"/></svg><svg><use href="#i-pool"/></svg><svg><use href="#i-bike"/></svg></div>
    <div class="card-foot"><div class="from">from<b>€ 3400</b>per week</div><div class="info-btn">+ Info</div></div>
  </div>
  <div class="abs card" style="left:670px;top:255px">
    <div class="card-photo" role="img" aria-label="Photo of a stone country house on a green lawn" style="background:linear-gradient(180deg,#6fa3d6 0%,#9a7a5a 40%,#8d6a48 65%,#4f8a2c 100%)"></div>
    <div class="card-title">Villa 2</div>
    <div class="card-type">Country House / Farm House</div>
    <div class="card-rule"></div>
    <div class="amen"><svg><use href="#i-wifi"/></svg><svg><use href="#i-snow"/></svg><svg><use href="#i-pool"/></svg><svg><use href="#i-bike"/></svg></div>
    <div class="card-foot"><div class="from">from<b>€ 4200</b>per week</div><div class="info-btn">+ Info</div></div>
  </div>

  <div class="abs card" style="left:282px;top:528px">
    <div class="card-photo" role="img" aria-label="Photo of an orange villa with a turquoise pool" style="background:linear-gradient(180deg,#5b9fe0 0%,#c8774a 38%,#4d8a3a 58%,#3fc4d8 100%)"></div>
    <div class="card-title">Agriturismo Il Sole</div>
    <div class="card-type">Vacation Home</div>
    <div class="card-rule"></div>
    <div class="amen"><svg><use href="#i-wifi"/></svg><svg><use href="#i-snow"/></svg><svg><use href="#i-pool"/></svg><svg><use href="#i-bike"/></svg></div>
    <div class="card-foot"><div class="from">from<b>€ 800</b>per week</div><div class="info-btn">+ Info</div></div>
  </div>
  <div class="abs card" style="left:476px;top:528px">
    <div class="card-photo" role="img" aria-label="Photo of a poolside table with a straw bag and hat" style="background:linear-gradient(180deg,#4e6b33 0%,#2d8fc4 40%,#c98e3e 75%,#8f6a3a 100%)"></div>
    <div class="card-title">Farmhouse In Tuscany</div>
    <div class="card-type">Vacation Home</div>
    <div class="card-rule"></div>
    <div class="amen"><svg><use href="#i-wifi"/></svg><svg><use href="#i-snow"/></svg><svg><use href="#i-pool"/></svg><svg><use href="#i-bike"/></svg></div>
    <div class="card-foot"><div class="from">from<b>€ 1300</b>per week</div><div class="info-btn">+ Info</div></div>
  </div>
  <div class="abs card" style="left:670px;top:528px">
    <div class="card-photo" role="img" aria-label="Photo of a pool in front of a farmhouse among olive trees" style="background:linear-gradient(180deg,#bcd4e6 0%,#5f7f45 40%,#38a6d6 72%,#a9a49a 100%)"></div>
    <div class="card-title">Appartmaneto Veneto</div>
    <div class="card-type">Villa</div>
    <div class="card-rule"></div>
    <div class="amen"><svg><use href="#i-wifi"/></svg><svg><use href="#i-snow"/></svg><svg><use href="#i-pool"/></svg><svg><use href="#i-bike"/></svg></div>
    <div class="card-foot"><div class="from">from<b>€ 4200</b>per week</div><div class="info-btn">+ Info</div></div>
  </div>

  <div class="abs showing">Showing 1 - 6 of 176 accommodations</div>
  <div class="abs pager"><span class="cur">1</span><span>2</span><span>3</span><span>4</span><span>›</span></div>

  <!-- footer -->
  <div class="abs footer"></div>
  <div class="abs f-brand"><span class="brand-mark"></span>StayNest</div>

  <div class="abs f-head" style="left:261px">Quick Links</div>
  <div class="abs f-link" style="left:261px;top:1020px">Home</div>
  <div class="abs f-link" style="left:261px;top:1042px">Search</div>
  <div class="abs f-link" style="left:261px;top:1063px">Property</div>
  <div class="abs f-link" style="left:261px;top:1085px">Custom</div>
  <div class="abs f-link" style="left:261px;top:1107px">Contact Us</div>

  <div class="abs f-head" style="left:408px">Company</div>
  <div class="abs f-link" style="left:408px;top:1020px">Privacy Policies</div>
  <div class="abs f-link" style="left:408px;top:1042px">Reservation Policies</div>
  <div class="abs f-link" style="left:408px;top:1063px">Cookie Policy</div>

  <div class="abs f-head" style="left:564px">Contact Us</div>
  <svg class="abs f-ico" style="left:565px;top:1022px"><use href="#i-pin"/></svg>
  <div class="abs f-link" style="left:580px;top:1020px;line-height:1.3">Via dei Tigli 7 50100<br>Valdorso (Italy)</div>
  <svg class="abs f-ico" style="left:565px;top:1062px"><use href="#i-phone"/></svg>
  <div class="abs f-link" style="left:579px;top:1061px">+39 000 1234567</div>
  <svg class="abs f-ico" style="left:565px;top:1091px"><use href="#i-mail"/></svg>
  <div class="abs f-link" style="left:580px;top:1089px">hello@staynest.example</div>

  <div class="abs f-head" style="left:771px">Follow Us</div>
  <div class="abs social" style="top:1022px"><i></i>Community</div>
  <div class="abs social" style="top:1048px"><i></i>Newsfeed</div>
  <div class="abs social" style="top:1075px"><i></i>Photo Feed</div>

  <div class="abs copy">Copyright © 2021 <b>StayNest</b>. All rights reserved.</div>
</div>
</body>
</html>
```